MIRDANE7 Research Outcomes (e-Toolkit)

I would like you to design an electronic document that can be used to display the outcomes of the MIRDANE7 Research that can easily be downloaded from a website. This document will help nurses, educators, students and their supervisors to be able to better understand the outcomes of the research and apply it to their own practice. It should be something they can print out (A4 size) and refer to easily. It should be quite graphical and represent male and female nurses working in different specialty areas (emergency, primary healthcare, aged care, etc.), across hospital to primary healthcare (community) contexts. It should be professional, clean and crisp in appearance. There are areas in yellow in the attached document that are yet to be determined. All images within the document can be amended to better reflect the design of the document and the intent of its contained content. An example of the type of document I'm looking for is attached as "standards.pdf". It should be approximately 15 pages in length.
Updates

The project does not have to use the MIRDANE7 logo or its colours as a main design feature of the project.

Target Market(s)

Nurses, educators and students.

Industry/Entity Type

Education

Font styles to use
Sans Serif

Colors

Designer to choose colors to be used in the design.

Requirements
Must have
• Must have a diagram depicting the interrelatedness of all the individual metaspecialties. The contained diagrams can be modified to suit graphic design needs.
• Images of nursing professionals should appear Australian.
Nice to have
• I would like them to try and re-configure the diagrams as they are boring and I hate the colours. Images of collaboration amongst different healthcare team members would be nice.
Should not have
• Only images of female nurses or only images (if chosen) of nurses only working in a hospital.

```html
<!DOCTYPE html>
<html lang="en">
<head>
<meta charset="utf-8">
<title>MIRDANE7 e-Toolkit – Section 2</title>
<link href="https://fonts.googleapis.com/css2?family=Barlow:wght@700&family=Quicksand:wght@400;500;700&display=swap" rel="stylesheet">
<style>
  :root{
    --teal:#3fb8a5;
    --teal-deep:#22a08e;
    --teal-soft:#a9ddd4;
    --ink:#4a4a4a;
    --ink-soft:#707070;
    --paper:#ffffff;
    --bg:#ecebe8;
  }
  *{box-sizing:border-box;margin:0;padding:0}
  html,body{width:1200px;height:756px;overflow:hidden;background:var(--bg)}
  .spread{position:relative;width:1200px;height:756px;display:flex}
  .page{position:relative;width:600px;height:756px;background:var(--paper);overflow:hidden;
        font-family:"Quicksand",sans-serif;color:var(--ink);font-size:11.6px;line-height:19.2px}
  .page--left{box-shadow:inset -18px 0 24px -18px rgba(0,0,0,.18)}
  .page--right{box-shadow:inset 18px 0 24px -18px rgba(0,0,0,.18)}
  .header-band{position:absolute;top:0;height:160px}
  .page--left .header-band{left:60px;right:0;
    background:linear-gradient(100deg,rgba(255,255,255,0) 0%,rgba(169,221,212,.45) 45%,rgba(63,184,165,.7) 100%);
    clip-path:polygon(0 0,100% 0,100% 55%,70% 100%,30% 40%)}
  .page--right .header-band{left:0;width:330px;
    background:linear-gradient(260deg,rgba(255,255,255,0) 0%,rgba(169,221,212,.5) 45%,rgba(63,184,165,.7) 100%);
    clip-path:polygon(0 0,100% 0,80% 45%,40% 100%,0 40%)}
  .section-title{position:absolute;left:149px;top:70px;font-family:"Barlow",sans-serif;font-weight:700;
    font-size:34px;line-height:41px;color:var(--teal);letter-spacing:.2px;text-transform:uppercase}
  .col{position:absolute}
  .col--l1{left:149px;top:173px;width:210px}
  .col--l2{left:373px;top:173px;width:215px}
  .col--r1{left:92px;top:168px;width:210px}
  .col--r2{left:306px;top:168px;width:215px}
  .standards-heading{font-weight:700}
  .standards-list{list-style:none}
  .standards-list li::before{content:"* "}
  .gap{height:19.2px}
  .figure{position:absolute;left:218px;top:466px;width:290px;height:242px}
  .figure-caption{position:absolute;left:149px;top:712px;font-size:7.5px;line-height:10px;color:var(--ink-soft)}
  .figure-caption b{color:var(--ink)}
  .page-number{position:absolute;bottom:18px;font-size:8px;color:var(--ink-soft)}
  .page--left .page-number{right:8px}
  .page--right .page-number{left:8px}
  .photo{position:absolute;left:306px;top:339px;width:294px;height:417px;
    background:linear-gradient(160deg,#dcdad6 0%,#cfcac4 45%,#b8b2aa 100%)}
  .diagram-label{font-family:"Quicksand",sans-serif;font-size:8px;fill:#fff;font-weight:500}
  .ring-text{font-family:"Quicksand",sans-serif;font-size:6px;fill:var(--ink)}
  .core-text{font-family:"Quicksand",sans-serif;font-size:14px;font-weight:700;fill:#8a8a8a}
</style>
</head>
<body>
<main class="spread">
  <section class="page page--left">
    <div class="header-band" role="img" aria-label="Teal geometric triangle pattern header"></div>
    <h1 class="section-title">Section 2:<br>How to use this toolkit</h1>

    <p class="col col--l1">The toolkit is based on a validated<br>metaspecialty taxonomy (see<br>Figure 1) that provides a framework<br>linking the metaspecialties to six<br>sets of specialty clinical standards<br>and complimentary to the national<br>Australian professional standards<br>for Nurse Practitioners (NPB ref).<br>The toolkit is to be used as resource<br>by nurse practitioner students, their<br>clinical mentors and university staff<br>teaching into nurse practitioner<br>Masters courses. It was developed<br>to assist identification of nurse<br>practitioner specialty clinical</p>

    <p class="col col--l2">learning and teaching needs during<br>periods of work based clinical<br>learning, now referred to in Australia<br>as Integrated Professional Practice<br>(ref). Based on feedback from<br>many nurse practitioners during<br>their widespread participation in<br>the Delphi studies that informed<br>this research, it became evident<br>that the clinical specialty standards<br>would also be useful for professional<br>development of endorsed nurse<br>practitioners seeking to expand their<br>clinical expertise.</p>

    <svg class="figure" viewBox="0 0 300 250" aria-label="The validated metaspecialty framework diagram">
      <defs>
        <path id="ring" d="M150,236 a111,111 0 1,1 0,-222 a111,111 0 1,1 0,222"/>
      </defs>
      <g fill="var(--teal)">
        <circle cx="150" cy="45" r="43"/><circle cx="219" cy="85" r="43"/>
        <circle cx="219" cy="165" r="43"/><circle cx="150" cy="205" r="43"/>
        <circle cx="81" cy="165" r="43"/><circle cx="81" cy="85" r="43"/>
      </g>
      <circle cx="150" cy="125" r="62" fill="#fff"/>
      <g class="photos">
        <circle cx="150" cy="42" r="36" fill="#e9e4df" role="img" aria-label="Photo of hands caring for an older patient"/>
        <circle cx="222" cy="83" r="36" fill="#8f8a86" role="img" aria-label="Photo of a supportive mental health conversation"/>
        <circle cx="222" cy="167" r="36" fill="#9a9896" role="img" aria-label="Photo of a patient with chronic illness"/>
        <circle cx="150" cy="208" r="36" fill="#cfcccb" role="img" aria-label="Photo of parent and child hands"/>
        <circle cx="78" cy="167" r="36" fill="#a7a8ad" role="img" aria-label="Photo of emergency care treatment"/>
        <circle cx="78" cy="83" r="36" fill="#7f8791" role="img" aria-label="Photo of a community health consultation"/>
      </g>
      <g class="diagram-label" text-anchor="middle">
        <text x="150" y="40">Aging &amp;</text><text x="150" y="50">Palliative Care</text>
        <text x="222" y="81">Mental Health</text><text x="222" y="91">Care</text>
        <text x="222" y="165">Chronic &amp;</text><text x="222" y="175">Complex Care</text>
        <text x="150" y="206">Child &amp; Family</text><text x="150" y="216">Health Care</text>
        <text x="78" y="165">Emergency &amp;</text><text x="78" y="175">Acute Care</text>
        <text x="78" y="81">Primary</text><text x="78" y="91">Health Care</text>
      </g>
      <text class="core-text" text-anchor="middle"><tspan x="150" y="122">Professional</tspan><tspan x="150" y="140">Standard</tspan></text>
      <g class="ring-text" text-anchor="middle">
        <text><textPath href="#ring" startOffset="8.33%">Clinical Practice Standard</textPath></text>
        <text><textPath href="#ring" startOffset="25%">Clinical Practice Standard</textPath></text>
        <text><textPath href="#ring" startOffset="41.67%">Clinical Practice Standard</textPath></text>
        <text><textPath href="#ring" startOffset="58.33%">Clinical Practice Standard</textPath></text>
        <text><textPath href="#ring" startOffset="75%">Clinical Practice Standard</textPath></text>
        <text><textPath href="#ring" startOffset="91.67%">Clinical Practice Standard</textPath></text>
      </g>
    </svg>
    <p class="figure-caption"><b>Figure 1:</b> The Validated Metaspecialty Framework</p>
    <span class="page-number">3|</span>
  </section>

  <section class="page page--right">
    <div class="header-band" role="img" aria-label="Teal geometric triangle pattern header"></div>

    <div class="col col--r1">
      <p>knowledge, skills and expertise.<br>These metaspecialty clinical<br>practice standards have been<br>developed and validated through<br>national research with nurse<br>practitioners to guide clinical<br>learning and teaching approaches<br>that support the development of an<br>advanced level of nursing practice<br>required for the nurse practitioner<br>role.</p>
      <p class="standards-heading">The six sets of clinical practice<br>standards are (in alphabetical<br>order):</p>
      <ul class="standards-list">
        <li>Ageing and palliative care,</li>
        <li>Child and family health care,</li>
        <li>Chronic and complex care,</li>
        <li>Emergency and acute care,</li>
        <li>Mental health care,</li>
        <li>Primary health care.</li>
      </ul>
      <div class="gap"></div>
      <p>The standards for the emergency<br>and acute care metaspecialty<br>comprise both acute care standards<br>developed as part of the MIRDANE7<br>study and some standards selected<br>from previous research by Dr Helen<br>Marlowe (Marlowe, 2015), which<br>used the same methodology<br>to develop emergency nurse</p>
    </div>

    <p class="col col--r2">practitioner clinical practice<br>standards. Dr Marlowe advised and<br>gave permission for these inclusions.<br>The remainder of the toolkit<br>describes how to use the toolkit and<br>then provides descriptions of each<br>metaspecialty followed by their<br>respective standards.</p>

    <div class="photo" role="img" aria-label="Photo of a clinician writing notes on a clipboard"></div>
    <span class="page-number">|2</span>
  </section>
</main>
</body>
</html>
```